Landscape design build company door flyer

I would like this flyer to convey a high-level of professionalism for a company that is excellent with communication with their clients as well as a company that does incredible installations

Went on vacation/holiday

```html
<!DOCTYPE html>
<html lang="en">
<head>
<meta charset="utf-8">
<title>Cedarline Builders – Outdoor Living Spaces Flyer</title>
<link href="https://fonts.googleapis.com/css2?family=Montserrat:wght@400;500;600;700;800&display=swap" rel="stylesheet">
<style>
  :root {
    --navy: #0c2a42;
    --navy-deep: #0a2438;
    --gold: #f7b500;
    --white: #ffffff;
    --paper: #f1f1f1;
    --stage: #e7e7e7;
    --ink: #12304a;
  }
  html, body {
    margin: 0; padding: 0;
    width: 1200px; height: 1029px;
    overflow: hidden;
    background: var(--stage);
    font-family: "Montserrat", Arial, sans-serif;
  }
  .flyer {
    position: absolute;
    left: 211px; top: 14px;
    width: 778px; height: 1000px;
    background: var(--white);
    box-shadow: 0 10px 30px rgba(0,0,0,.25);
    overflow: hidden;
  }
  .hero {
    position: absolute; left: 0; top: 49px;
    width: 778px; height: 654px;
    background: var(--navy);
  }
  .brand-tab { position: absolute; left: 0; top: 0; }
  .brand-name {
    position: absolute; left: 291px; top: 101px; width: 187px;
    text-align: center; color: var(--ink);
    font-weight: 700; font-size: 14px; letter-spacing: .2px;
    margin: 0;
  }
  .brand-tagline {
    position: absolute; left: 291px; top: 120px; width: 187px;
    text-align: center; color: var(--ink);
    font-weight: 600; font-size: 7px; letter-spacing: .1px;
    margin: 0;
  }
  .headline {
    position: absolute; left: 0; top: 121px; width: 778px;
    margin: 0; text-align: center;
    color: var(--white); font-weight: 800;
    font-size: 44px; line-height: 46px; letter-spacing: .3px;
  }
  .headline .accent { color: var(--gold); }
  .about-title {
    position: absolute; left: 61px; top: 300px; margin: 0;
    color: var(--white); font-weight: 600; font-size: 18px; line-height: 22px;
  }
  .about-copy {
    position: absolute; left: 61px; top: 331px; width: 272px;
    color: var(--white); font-size: 11.2px; line-height: 14.8px;
    text-align: justify; hyphens: manual;
  }
  .about-copy p { margin: 0 0 14.8px; }
  .about-copy p:last-child { margin-bottom: 0; }
  .photo { position: absolute; }
  .photo-deck    { left: 369px; top: 306px; width: 130px; height: 130px; background: linear-gradient(160deg,#3f7a33,#8a4a2e 70%,#6b3822); }
  .photo-kitchen { left: 510px; top: 306px; width: 208px; height: 130px; background: linear-gradient(180deg,#8a5a36,#5d5f5c 50%,#3f4246); }
  .photo-pool    { left: 369px; top: 446px; width: 130px; height: 91px; background: linear-gradient(180deg,#d9dfe0,#9fb8a6 50%,#3fb0a8); }
  .photo-steps   { left: 369px; top: 547px; width: 130px; height: 91px; background: linear-gradient(180deg,#5a6a3a,#6c6e70 40%,#4a4c4f); }
  .photo-firepit { left: 510px; top: 446px; width: 208px; height: 192px; background: linear-gradient(180deg,#4a6fa8,#284a7a 40%,#2b3345 60%,#5a4a40); }
  .services {
    position: absolute; left: 0; top: 703px; width: 778px; height: 174px;
    background: linear-gradient(90deg,#ffffff 0%,#ffffff 45%,#c9ccd0 72%,#4a5d6f 92%,#2a4258 100%);
  }
  .services-title {
    position: absolute; left: 61px; top: 11px; margin: 0;
    color: var(--ink); font-weight: 700; font-size: 18px; line-height: 22px;
  }
  .service-list { list-style: none; margin: 0; padding: 0; }
  .service {
    position: absolute; display: flex; align-items: center; gap: 8px;
    color: var(--ink); font-weight: 700; font-size: 11px; white-space: nowrap;
  }
  .service svg { width: 28px; height: 28px; flex: none; }
  .seal { position: absolute; left: 601px; top: 35px; }
  .contact {
    position: absolute; left: 0; top: 877px; width: 778px; height: 117px;
    background: var(--navy-deep);
  }
  .contact-title {
    position: absolute; left: 61px; top: 15px; margin: 0;
    color: var(--white); font-weight: 600; font-size: 16px; line-height: 20px;
  }
  .contact-phone {
    position: absolute; left: 61px; top: 36px;
    display: flex; align-items: center; gap: 14px;
    color: var(--gold); font-weight: 700; font-size: 41px; line-height: 52px;
  }
  .contact-email {
    position: absolute; right: 30px; top: 48px;
    color: var(--white); font-size: 15.5px; letter-spacing: .3px;
  }
</style>
</head>
<body>
<main class="flyer">
  <section class="hero">
    <h1 class="headline">LET’S CREATE<br><span class="accent">YOUR DREAM OUTDOOR</span><br>LIVING SPACE!</h1>
    <h2 class="about-title">ABOUT US</h2>
    <div class="about-copy">
      <p>Discover the endless possibilities for your outdoor space with The Cedarline Builders Team. Our team of skilled artisans is dedi&shy;cated to turning your outdoor space into a breathtaking oasis that you’ll love coming home to. Whether it’s a cozy patio for intimate gatherings, a sprawling deck to host memorable parties, or a custom paver driveway that adds instant curb appeal, our high-quality craftsmanship ensures stunning results that exceed your expec&shy;tations.</p>
      <p>From concept to completion, we take pride in every detail, using the finest mate&shy;rials to withstand Seattle’s climate while adding timeless elegance to your property. Embrace the Pacific Northwest lifestyle and create cherished moments with family and friends in a captivating outdoor haven.</p>
    </div>
    <div class="photo photo-deck" role="img" aria-label="Wooden deck with pergola and patio chairs"></div>
    <div class="photo photo-kitchen" role="img" aria-label="Covered outdoor kitchen with stone fireplace"></div>
    <div class="photo photo-pool" role="img" aria-label="Backyard swimming pool beside a modern home"></div>
    <div class="photo photo-steps" role="img" aria-label="Stone retaining wall with steps"></div>
    <div class="photo photo-firepit" role="img" aria-label="Lakeside paver patio with fire pit and lounge chairs at dusk"></div>
  </section>

  <svg class="brand-tab" width="778" height="175" viewBox="0 0 778 175" aria-hidden="true">
    <polygon points="229,0 541,0 541,49 478,137 291,137 229,49" fill="#f0f0f0"/>
    <rect x="291" y="0" width="187" height="137" fill="#ffffff"/>
    <line x1="291.5" y1="137" x2="291.5" y2="170" stroke="#000" stroke-width="1"/>
    <line x1="477.5" y1="137" x2="477.5" y2="170" stroke="#000" stroke-width="1"/>
  </svg>
  <p class="brand-name">CEDARLINE BUILDERS</p>
  <p class="brand-tagline">OUTDOOR LIVING SPACES</p>

  <section class="services">
    <h2 class="services-title">OUR SERVICES</h2>
    <ul class="service-list">
      <li class="service" style="left:62px;top:54px"><svg viewBox="0 0 28 28"><path d="M3 12 L14 3 L25 12 V26 H3 Z" fill="none" stroke="#12304a" stroke-width="2"/><path d="M9 15 h10 M14 12 v10 M10 22 h8" stroke="#12304a" stroke-width="1.6"/></svg>Paver Patios</li>
      <li class="service" style="left:62px;top:93px"><svg viewBox="0 0 28 28"><path d="M3 12 L14 3 L25 12 V26 H3 Z" fill="none" stroke="#12304a" stroke-width="2"/><path d="M6 23 L11 15 H17 L22 23 Z" fill="#12304a"/></svg>Paver Driveways</li>
      <li class="service" style="left:62px;top:134px"><svg viewBox="0 0 28 28"><path d="M3 12 L14 3 L25 12 V26 H3 Z" fill="none" stroke="#12304a" stroke-width="2"/><path d="M8 13 h8 v3 h3 v3 h-3 v4 h-4 v-4 h-4 Z" fill="#12304a"/></svg>Retaining Walls</li>
      <li class="service" style="left:228px;top:54px"><svg viewBox="0 0 28 28"><path d="M3 12 L14 3 L25 12 V26 H3 Z" fill="none" stroke="#12304a" stroke-width="2"/><path d="M10 11 v8 M16 11 v8 M10 15 h6 M7 21 q2 -2 4 0 t4 0 t4 0 t4 0" fill="none" stroke="#12304a" stroke-width="1.6"/></svg>Pools</li>
      <li class="service" style="left:228px;top:93px"><svg viewBox="0 0 28 28"><path d="M3 12 L14 3 L25 12 V26 H3 Z" fill="none" stroke="#12304a" stroke-width="2"/><path d="M8 13 h12 M8 13 v10 M20 13 v10 M11 16 v7 M14 16 v7 M17 16 v7 M8 19 h12" stroke="#12304a" stroke-width="1.5"/></svg>Decks &amp; Railings</li>
      <li class="service" style="left:228px;top:134px"><svg viewBox="0 0 28 28"><path d="M3 12 L14 3 L25 12 V26 H3 Z" fill="none" stroke="#12304a" stroke-width="2"/><path d="M8 17 L14 11 L20 17 V23 H8 Z" fill="#12304a"/><rect x="12" y="18" width="4" height="5" fill="#fff"/></svg>Firepits &amp; Fireplaces</li>
      <li class="service" style="left:400px;top:54px"><svg viewBox="0 0 28 28"><path d="M3 12 L14 3 L25 12 V26 H3 Z" fill="none" stroke="#12304a" stroke-width="2"/><path d="M11 11 h6 l-1 6 h-4 Z M14 17 v6" fill="none" stroke="#12304a" stroke-width="1.6"/></svg>Outdoor Lighting</li>
      <li class="service" style="left:400px;top:93px"><svg viewBox="0 0 28 28"><path d="M3 12 L14 3 L25 12 V26 H3 Z" fill="none" stroke="#12304a" stroke-width="2"/><circle cx="14" cy="17" r="5" fill="none" stroke="#12304a" stroke-width="1.5"/><path d="M14 14 v6 M11 17 h6" stroke="#12304a" stroke-width="1.5"/></svg>And More...</li>
    </ul>
    <svg class="seal" width="118" height="118" viewBox="0 0 118 118" role="img" aria-label="Experience seal">
      <circle cx="59" cy="59" r="58" fill="#1c1a12"/>
      <circle cx="59" cy="59" r="54" fill="#d4a92a"/>
      <circle cx="59" cy="59" r="40" fill="#b88a18" stroke="#f1d27a" stroke-width="2"/>
    </svg>
  </section>

  <section class="contact">
    <h2 class="contact-title">CONTACT US TODAY</h2>
    <div class="contact-phone">
      <svg width="36" height="36" viewBox="0 0 24 24" aria-hidden="true"><path d="M6.6 10.8a15.1 15.1 0 0 0 6.6 6.6l2.2-2.2a1 1 0 0 1 1-.25 11.4 11.4 0 0 0 3.6.57 1 1 0 0 1 1 1V20a1 1 0 0 1-1 1A17 17 0 0 1 3 4a1 1 0 0 1 1-1h3.5a1 1 0 0 1 1 1c0 1.25.2 2.46.57 3.6a1 1 0 0 1-.25 1z" fill="#f7b500"/><path d="M14 3.5a7 7 0 0 1 6.5 6.5 M14 6.8a3.8 3.8 0 0 1 3.2 3.2" fill="none" stroke="#f7b500" stroke-width="1.6" stroke-linecap="round"/></svg>
      <span>[206]-555-0148</span>
    </div>
    <div class="contact-email">info@cedarlinebuilders.com</div>
  </section>
</main>
</body>
</html>
```